RWT Fittings Ltd Business Cards

We need a business card with our business logo. We provide window and door installations on high-rises in west coast British Colombia, Canada.

I would like my business information and details on one side of the card, and the other side the company name with logo

Target Market(s)

General Contractors

Industry/Entity Type

Construction

Contact Information for Business Card

one side i want my company name and logo in the dark theme logo that i provided

Requirements
Must have
• Marco Peltieri, 16045518293, RWTFittings@mailbox-demo.com, 1407-5194 Linden Row Burnaby BC, V5H 2K9, Owner & Manager

```html
<!DOCTYPE html>
<html lang="en">
<head>
<meta charset="utf-8">
<title>RWT Fittings Ltd – Business Cards</title>
<link href="https://fonts.googleapis.com/css2?family=Roboto:wght@400;500;700;900&display=swap" rel="stylesheet">
<style>
  :root {
    --backdrop: #242424;
    --card-dark: #202126;
    --brand-blue: #29abe2;
    --brand-blue-light: #4cc3e6;
    --brand-grey: #9a9a9a;
    --text-white: #ffffff;
    --scene-warm: #57504b;
    --scene-deep: #1d1b1a;
  }
  * { margin: 0; padding: 0; box-sizing: border-box; }
  html, body {
    width: 1200px; height: 780px; overflow: hidden;
    background: var(--backdrop);
    font-family: "Roboto", Arial, sans-serif;
  }
  .sheet {
    position: relative; width: 1200px; height: 780px;
    display: flex; align-items: center; justify-content: center; gap: 40px;
  }
  .card {
    position: relative; width: 540px; height: 309px; overflow: hidden;
    background: var(--card-dark);
    box-shadow: 0 18px 40px rgba(0,0,0,.55);
  }
  .card-swoosh { position: absolute; inset: 0; }

  /* front: company mark + contact details */
  .brand {
    position: absolute; left: 30px; top: 136px;
    display: flex; align-items: center; gap: 10px;
  }
  .brand-square { width: 16px; height: 16px; background: var(--brand-grey); }
  .brand-name {
    font-weight: 700; font-size: 21px; color: var(--brand-blue);
    white-space: nowrap;
  }
  .divider {
    position: absolute; left: 250px; top: 62px;
    width: 2px; height: 150px; background: var(--text-white);
  }
  .contact { position: absolute; left: 274px; top: 52px; color: var(--text-white); }
  .contact-name { font-weight: 900; font-size: 26px; line-height: 1.05; }
  .contact-name .first { color: var(--brand-blue); }
  .contact-name .last { color: var(--brand-grey); }
  .contact-role { font-weight: 700; font-size: 13px; margin-top: 2px; }
  .contact-address { font-size: 13.5px; line-height: 1.3; margin-top: 14px; }
  .contact-lines { margin-top: 12px; }
  .contact-line { display: flex; align-items: center; gap: 7px; font-size: 13px; line-height: 1.5; }
  .contact-line svg { width: 14px; height: 14px; flex: none; }

  /* back: company name on scene backdrop */
  .card-back { background: var(--scene-deep); }
  .scene-fill {
    position: absolute; inset: 0;
    background: radial-gradient(ellipse at 65% 35%, var(--scene-warm) 0%, #3a3532 45%, var(--scene-deep) 100%);
  }
  .back-brand {
    position: absolute; inset: 0;
    display: flex; align-items: center; justify-content: center; gap: 14px;
  }
  .back-brand .brand-square { width: 26px; height: 26px; }
  .back-brand .brand-name { font-size: 36px; color: var(--brand-blue-light); }
</style>
</head>
<body>
<main class="sheet">
  <section class="card card-front">
    <svg class="card-swoosh" viewBox="0 0 540 309" preserveAspectRatio="none" aria-hidden="true">
      <path d="M0,309 L0,262 C170,250 390,212 540,268 L540,309 Z" fill="var(--brand-blue)"/>
      <path d="M330,244 C420,218 495,222 540,252" fill="none" stroke="var(--brand-grey)" stroke-width="4"/>
    </svg>

    <div class="brand">
      <span class="brand-square"></span>
      <span class="brand-name">RWT Fittings Ltd</span>
    </div>

    <div class="divider"></div>

    <div class="contact">
      <div class="contact-name"><span class="first">Marco</span> <span class="last">Peltieri</span></div>
      <div class="contact-role">Owner &amp; Manager</div>
      <div class="contact-address">1407-5194 Linden Row<br>Burnaby BC, V5H 2K9</div>
      <div class="contact-lines">
        <div class="contact-line">
          <svg viewBox="0 0 24 24"><path d="M6.6 10.8a15 15 0 0 0 6.6 6.6l2.2-2.2a1 1 0 0 1 1-.25 11.4 11.4 0 0 0 3.6.57 1 1 0 0 1 1 1V20a1 1 0 0 1-1 1A17 17 0 0 1 3 4a1 1 0 0 1 1-1h3.5a1 1 0 0 1 1 1c0 1.25.2 2.45.57 3.57a1 1 0 0 1-.25 1z" fill="var(--brand-blue)"/></svg>
          <span>1604 551 8293</span>
        </div>
        <div class="contact-line">
          <svg viewBox="0 0 24 24"><rect x="2" y="5" width="20" height="14" rx="1.5" fill="var(--brand-blue)"/><path d="M3 6.5l9 6.5 9-6.5" fill="none" stroke="var(--card-dark)" stroke-width="1.8"/></svg>
          <span>RWTFittings@mailbox-demo.com</span>
        </div>
      </div>
    </div>
  </section>

  <section class="card card-back">
    <div class="scene-fill" role="img" aria-label="Softly blurred photograph of an office interior with a plant, in warm dark grey tones"></div>
    <div class="back-brand">
      <span class="brand-square"></span>
      <span class="brand-name">RWT Fittings Ltd</span>
    </div>
  </section>
</main>
</body>
</html>
```